QVR business card

Need a business card for a company that provides instructional design and elearning development services. The website is here: http://quorvane.studio/

I'm attaching a current logo, as well as the old business card design. While I like to keep it clean, the old design is too simplistic for my liking. The only idea I want to reuse from the old design is placing industry jargon on the back of the card, just need a better way to present it. But if you have other ideas for the back--feel free to experiment.

Please use the colors complementary to the color we have on the website. Thank you!

```html
<!DOCTYPE html>
<html lang="en">
<head>
<meta charset="utf-8">
<title>QVR business card</title>
<link rel="stylesheet" href="https://fonts.googleapis.com/css2?family=Source+Sans+3:wght@400;600;700&display=swap">
<style>
  :root {
    --teal: #14b2b0;
    --teal-deep: #0fa6a6;
    --sand: #dccf96;
    --sand-light: #e4dba6;
    --ink: #2a2a2a;
    --paper: #ffffff;
    --stage: #e6e6e4;
  }
  * { box-sizing: border-box; margin: 0; padding: 0; }
  html, body { width: 1200px; height: 907px; overflow: hidden; }
  body {
    background: var(--stage);
    font-family: "Source Sans 3", "Myriad Pro", Arial, sans-serif;
    position: relative;
  }
  .card {
    position: absolute;
    width: 540px;
    height: 310px;
    overflow: hidden;
    box-shadow: 0 8px 24px rgba(0,0,0,.18);
  }

  /* Front */
  .card-front { left: 40px; top: 120px; background: var(--paper); }
  .front-shapes { position: absolute; inset: 0; }
  .brand {
    position: absolute; left: 48px; bottom: 62px;
    display: flex; align-items: center; gap: 12px;
  }
  .brand-dot { width: 26px; height: 26px; border-radius: 50%; background: var(--teal); }
  .brand-name { font-size: 46px; font-weight: 700; color: var(--teal); letter-spacing: 1px; }
  .person { position: absolute; left: 300px; top: 30px; }
  .person-name {
    font-size: 19px; font-weight: 700; color: var(--sand-light);
    letter-spacing: 1.5px; text-transform: uppercase;
  }
  .person-role { font-size: 15px; color: var(--ink); margin-top: 1px; }
  .contact-icons {
    position: absolute; left: 326px; top: 180px;
    display: flex; flex-direction: column; gap: 4px;
  }
  .contact-icons svg { width: 18px; height: 18px; display: block; }
  .contacts {
    position: absolute; left: 354px; right: 24px; top: 178px;
    list-style: none; color: var(--paper); font-size: 13.5px; line-height: 22px;
    white-space: nowrap;
  }

  /* Back */
  .card-back {
    left: 620px; top: 470px;
    background: linear-gradient(135deg, var(--teal) 0%, #7cc3ac 45%, var(--sand) 100%);
  }
  .map-area {
    position: absolute; left: 200px; top: 60px; width: 320px; height: 200px;
    border-radius: 40px;
    background: radial-gradient(ellipse at center, rgba(70,130,110,.18), rgba(70,130,110,0) 70%);
  }
  .back-brand {
    position: absolute; left: 0; right: 0; top: 52px; text-align: center;
    font-size: 52px; font-weight: 700; color: var(--paper); letter-spacing: 2px;
  }
  .services {
    position: absolute; left: 0; right: 0; top: 138px;
    display: flex; flex-direction: column; align-items: center; gap: 7px; list-style: none;
  }
  .service {
    background: var(--teal-deep); color: var(--paper);
    font-size: 17px; padding: 1px 8px; border-radius: 3px;
  }
  .back-url {
    position: absolute; left: 0; right: 0; bottom: 38px; text-align: center;
    color: var(--paper); font-size: 15px; letter-spacing: .5px;
  }
</style>
</head>
<body>

<section class="card card-front" aria-label="Business card front">
  <svg class="front-shapes" viewBox="0 0 540 310" preserveAspectRatio="none" aria-hidden="true">
    <path d="M250 0 H540 V310 H360 C340 250 330 215 300 200 C300 120 280 60 250 0 Z" fill="#dccf96"/>
    <path d="M272 0 H540 V300 C470 300 420 290 385 275 C360 235 345 200 322 178 C320 110 300 55 272 0 Z" fill="#14b2b0"/>
  </svg>

  <div class="brand">
    <span class="brand-dot"></span>
    <span class="brand-name">QVR</span>
  </div>

  <div class="person">
    <p class="person-name">Marcus Delvane</p>
    <p class="person-role">Managing Director</p>
  </div>

  <div class="contact-icons" aria-hidden="true">
    <svg viewBox="0 0 18 18"><circle cx="9" cy="9" r="9" fill="#0fa6a6"/><path d="M6 5 l2 0 1 3 -1.3 1 a6 6 0 0 0 2.3 2.3 l1 -1.3 3 1 0 2 c-4 1 -9 -4 -8 -8z" fill="#fff"/></svg>
    <svg viewBox="0 0 18 18"><circle cx="9" cy="9" r="9" fill="#0fa6a6"/><rect x="4.5" y="6" width="9" height="6.5" fill="#fff"/><path d="M4.5 6 L9 10 L13.5 6" stroke="#0fa6a6" fill="none"/></svg>
    <svg viewBox="0 0 18 18"><circle cx="9" cy="9" r="9" fill="#0fa6a6"/><circle cx="9" cy="9" r="5" fill="none" stroke="#fff"/><path d="M4 9 H14 M9 4 C6 7 6 11 9 14 M9 4 C12 7 12 11 9 14" stroke="#fff" fill="none"/></svg>
  </div>

  <ul class="contacts">
    <li>555-013-2870</li>
    <li>mdelvane@quorvane.studio</li>
    <li>www.quorvane.studio</li>
  </ul>
</section>

<section class="card card-back" aria-label="Business card back">
  <div class="map-area" role="img" aria-label="Dotted world map in soft green tones"></div>
  <p class="back-brand">QVR</p>
  <ul class="services">
    <li class="service">Instructional Design</li>
    <li class="service">Elearning Development | Mobile Learning</li>
    <li class="service">Insructor-LED Training</li>
  </ul>
  <p class="back-url">www.quorvane.studio</p>
</section>

</body>
</html>
```